Need Business Card for eLearning Company

Need a business card designed for our company, CareerVantly.

CareerVantly has developed a complete 12 lesson eLearning course to teach you the skills you need to present yourself in a job interview. The course uses advanced learning techniques in the multimedia videos, plus contains quizzes and additional exercises to insure you get the course and can walk into any interview with confidence and ease, and get the job.

www.careervantly-example.com

Industry/Entity Type

Business

```html
<!DOCTYPE html>
<html lang="en">
<head>
<meta charset="utf-8">
<title>CareerVantly Business Card</title>
<link rel="stylesheet" href="https://fonts.googleapis.com/css2?family=Jost:wght@300;400;600&display=swap">
<style>
  :root {
    --plum: #7b1769;
    --leaf: #7a9c1e;
    --card-light: #ececec;
    --ink: #3a3a3a;
    --page: #e2e0dc;
    --white: #ffffff;
  }
  * { box-sizing: border-box; margin: 0; padding: 0; }
  html, body {
    width: 1200px;
    height: 900px;
    overflow: hidden;
    background: var(--page);
    font-family: "Jost", sans-serif;
  }
  .sheet {
    width: 1200px;
    height: 900px;
    display: flex;
    flex-direction: column;
    align-items: center;
    justify-content: center;
    gap: 50px;
  }
  .card {
    width: 600px;
    height: 343px;
    position: relative;
    overflow: hidden;
    box-shadow: 0 6px 18px rgba(0,0,0,0.18);
  }

  /* Front */
  .card-front {
    background: var(--plum);
    display: flex;
    flex-direction: column;
    align-items: center;
    justify-content: center;
    color: var(--white);
  }
  .brand {
    display: flex;
    align-items: center;
    gap: 14px;
  }
  .brand-mark {
    width: 22px;
    height: 22px;
    background: var(--white);
  }
  .brand-name {
    font-weight: 300;
    font-size: 46px;
    letter-spacing: 0.5px;
    line-height: 1;
  }
  .brand-rule {
    width: 260px;
    height: 1px;
    background: rgba(255,255,255,0.7);
    margin: 12px 0 8px;
  }
  .tagline {
    font-weight: 400;
    font-size: 12px;
    letter-spacing: 2.5px;
    text-transform: uppercase;
  }

  /* Back */
  .card-back {
    background: var(--card-light);
  }
  .bubble-field {
    position: absolute;
    left: 0;
    bottom: 0;
    width: 300px;
    height: 230px;
  }
  .contact {
    position: absolute;
    left: 300px;
    top: 38px;
    width: 270px;
    color: var(--ink);
  }
  .person-name {
    color: var(--plum);
    font-weight: 400;
    font-size: 22px;
    line-height: 1.1;
  }
  .person-title {
    font-weight: 400;
    font-size: 14px;
    letter-spacing: 1px;
    text-transform: uppercase;
    margin-top: 2px;
  }
  .contact-rule {
    height: 1.5px;
    background: var(--plum);
    margin: 10px 0 18px;
  }
  .contact-lines {
    list-style: none;
    font-size: 12px;
    line-height: 1.45;
  }
  .contact-lines .label {
    color: var(--plum);
    display: inline-block;
    width: 14px;
  }
  .address {
    font-style: normal;
    font-size: 12px;
    line-height: 1.45;
    margin-top: 18px;
  }
  .website {
    position: absolute;
    right: 30px;
    bottom: 30px;
    color: var(--plum);
    font-weight: 600;
    font-size: 14px;
    text-decoration: none;
  }
</style>
</head>
<body>
<main class="sheet">

  <section class="card card-front" aria-label="Business card front">
    <div class="brand">
      <span class="brand-mark"></span>
      <span class="brand-name">careervantly</span>
    </div>
    <div class="brand-rule"></div>
    <p class="tagline">Growing your next role</p>
  </section>

  <section class="card card-back" aria-label="Business card back">
    <svg class="bubble-field" viewBox="0 0 300 230" role="img" aria-label="Cluster of purple and green speech bubbles">
      <defs>
        <linearGradient id="bubbleTones" x1="0" y1="0" x2="1" y2="1">
          <stop offset="0" stop-color="#7a9c1e"/>
          <stop offset="0.5" stop-color="#7b1769"/>
          <stop offset="1" stop-color="#7a9c1e"/>
        </linearGradient>
      </defs>
      <rect x="0" y="0" width="300" height="230" fill="url(#bubbleTones)" opacity="0.85"/>
    </svg>

    <div class="contact">
      <h1 class="person-name">Dana Whitfield</h1>
      <p class="person-title">Principal Consultant</p>
      <div class="contact-rule"></div>
      <ul class="contact-lines">
        <li><span class="label">T</span>(555) 014-2386</li>
        <li><span class="label">E</span>support@careervantly-example.com</li>
      </ul>
      <address class="address">
        420 Harbor Lane NE Suite 12,<br>
        Lakeview, WA 98000
      </address>
    </div>

    <a class="website" href="#">www.careervantly-example.com</a>
  </section>

</main>
</body>
</html>
```